Cobalt Ridge Electric Needs A Logo Design

We need a logo for my new company based out of Sacramento, Ca called Cobalt Ridge Electric. The name says it all, my electrical contracting business provides "Cobalt Ridge Professional Work" I'm open to any colors that pop and customers to say Wow. I would love to print my cards on metal.

Industry/Entity Type

Business

Contact Information for Business Card

The card needs to have as follows
Name of company: Cobalt Ridge Electric
My Name: Marco Delvane
Phone # 916-555-0173
CL# 2049381
Email: cobaltridgeelectric@mailnest.example
and a slogan that represent "COBALT RIDGE"

Requirements
Must have
• The card needs to have as follows
• Name of company: Cobalt Ridge Electric
• My Name : Marco Delvane
• Phone # 916-555-0173
• CL# 2049381
• Email: cobaltridgeelectric@mailnest.example
• and a slogan that represent "COBALT RIDGE"
Nice to have
• popping colors
• electrical Arcing

```html
<!DOCTYPE html>
<html lang="en">
<head>
<meta charset="utf-8">
<title>Cobalt Ridge Electric — Business Card</title>
<link rel="stylesheet" href="https://fonts.googleapis.com/css2?family=Montserrat:wght@700&family=Quicksand:wght@400;500&display=swap">
<style>
  :root {
    --page-bg: #e4e1dc;
    --card-black: #0b0b0c;
    --card-sheen: #2a2b2e;
    --cobalt: #1a7cc1;
    --steel: #a9abae;
    --ink-light: #e6e7e9;
    --ink-muted: #b9bbbf;
    --rule: #f2f2f2;
  }
  * { margin: 0; padding: 0; box-sizing: border-box; }
  html, body {
    width: 1200px;
    height: 1022px;
    overflow: hidden;
    background: var(--page-bg);
  }
  .card {
    position: absolute;
    left: 100px;
    top: 225px;
    width: 1000px;
    height: 572px;
    background: linear-gradient(125deg, var(--card-black) 0%, var(--card-sheen) 48%, var(--card-black) 72%);
    border-radius: 6px;
    overflow: hidden;
    box-shadow: 0 18px 40px rgba(0,0,0,0.28);
  }
  .card-bands {
    position: absolute;
    inset: 0;
  }
  .brand {
    position: absolute;
    left: 64px;
    top: 62px;
    display: flex;
    align-items: center;
    gap: 22px;
  }
  .brand-square {
    width: 70px;
    height: 70px;
    background: var(--cobalt);
  }
  .brand-name {
    font-family: "Quicksand", sans-serif;
    font-weight: 500;
    font-size: 50px;
    line-height: 1.02;
    letter-spacing: 3px;
    color: var(--ink-light);
  }
  .slogan {
    position: absolute;
    left: 156px;
    top: 180px;
    font-family: "Quicksand", sans-serif;
    font-weight: 500;
    font-size: 18px;
    letter-spacing: 2px;
    color: var(--ink-muted);
  }
  .holder-name {
    position: absolute;
    right: 110px;
    top: 236px;
    font-family: "Montserrat", sans-serif;
    font-weight: 700;
    font-size: 30px;
    letter-spacing: 2px;
    color: var(--cobalt);
  }
  .divider {
    position: absolute;
    left: 360px;
    right: 90px;
    top: 292px;
    height: 3px;
    background: var(--rule);
  }
  .contact-list {
    position: absolute;
    left: 360px;
    top: 318px;
    list-style: none;
    font-family: "Quicksand", sans-serif;
    font-weight: 500;
    font-size: 25px;
    line-height: 40px;
    color: var(--ink-light);
  }
  .contact-item {
    display: flex;
    align-items: center;
    gap: 14px;
  }
  .contact-icon {
    width: 18px;
    height: 18px;
    flex: none;
  }
</style>
</head>
<body>
  <main class="card">
    <svg class="card-bands" width="1000" height="572" viewBox="0 0 1000 572" aria-hidden="true">
      <polygon class="band-steel" points="0,540 664,540 646,572 0,572" fill="#a9abae"/>
      <polygon class="band-cobalt" points="646,572 696,482 1000,482 1000,572" fill="#1a7cc1"/>
    </svg>

    <div class="brand">
      <div class="brand-square"></div>
      <div class="brand-name">COBALT RIDGE<br>ELECTRIC</div>
    </div>
    <p class="slogan">Cobalt Ridge Professional Work</p>

    <div class="holder-name">MARCO DELVANE</div>
    <div class="divider"></div>

    <ul class="contact-list">
      <li class="contact-item">
        <svg class="contact-icon" viewBox="0 0 18 18" aria-hidden="true"><rect x="2" y="2" width="14" height="14" rx="2" fill="none" stroke="#1a7cc1" stroke-width="2"/></svg>
        <span>2049381</span>
      </li>
      <li class="contact-item">
        <svg class="contact-icon" viewBox="0 0 18 18" aria-hidden="true"><path d="M4 2 L7 2 L8 6 L6 7.5 C7 10 8 11 10.5 12 L12 10 L16 11 L16 14 C16 15 15 16 14 16 C8 16 2 10 2 4 C2 3 3 2 4 2 Z" fill="#1a7cc1"/></svg>
        <span>916-555-0173</span>
      </li>
      <li class="contact-item">
        <svg class="contact-icon" viewBox="0 0 18 18" aria-hidden="true"><rect x="1.5" y="3.5" width="15" height="11" rx="1.5" fill="none" stroke="#1a7cc1" stroke-width="2"/><path d="M2 4.5 L9 10 L16 4.5" fill="none" stroke="#1a7cc1" stroke-width="2"/></svg>
        <span>cobaltridgeelectric@mailnest.example</span>
      </li>
    </ul>
  </main>
</body>
</html>
```